Employee Benefits and Insurance Consulting

We are an existing company with over 30 years experience but are changing our name. We would like a simple design with grey tones.

Industry/Entity Type

Insurance

Contact Information for Business Card

Marlow Benefits Consulting
Gerald P Hollins CEO
5172 Brackenridge Road
Ashford, TN 37990
gerald@marlowbenefits-example.com
865-412-5593 - O
865-247-3861 - C

```html
<!DOCTYPE html>
<html lang="en">
<head>
<meta charset="utf-8">
<title>Marlow Benefits Consulting – Business Card</title>
<link href="https://fonts.googleapis.com/css2?family=Source+Sans+3:wght@400;600&display=swap" rel="stylesheet">
<style>
  :root {
    --backdrop: #000000;
    --card: #323335;
    --teal: #2b9d93;
    --light: #f2f2f2;
    --rule: #47494c;
  }
  html, body {
    margin: 0;
    padding: 0;
    width: 1200px;
    height: 900px;
    overflow: hidden;
    background: var(--backdrop);
    font-family: "Source Sans 3", "Myriad Pro", sans-serif;
  }
  .canvas {
    position: relative;
    width: 1200px;
    height: 900px;
  }
  .card {
    position: absolute;
    top: 271px;
    width: 456px;
    height: 281px;
    border-radius: 14px;
    background: var(--card);
  }
  .card--front { left: 137px; }
  .card--back { left: 627px; }

  .brand-block {
    position: absolute;
    left: 40px;
    top: 104px;
    width: 150px;
    color: var(--teal);
    font-weight: 600;
    font-size: 24px;
    line-height: 1.1;
  }
  .divider {
    position: absolute;
    left: 218px;
    top: 68px;
    width: 1px;
    height: 148px;
    background: var(--rule);
  }
  .details {
    position: absolute;
    left: 236px;
    top: 70px;
    color: var(--light);
    font-size: 13px;
    line-height: 17px;
  }
  .person {
    margin: 0 0 17px;
    color: var(--teal);
    font-weight: 600;
    font-size: 17px;
    line-height: 22px;
  }
  .person .role { font-size: 12px; }
  .address { margin: 0 0 14px; }
  .contacts { list-style: none; margin: 0; padding: 0; }
  .contacts li {
    display: flex;
    align-items: center;
    height: 19px;
    font-size: 12.5px;
    white-space: nowrap;
  }
  .contacts li.email { font-size: 12px; }
  .contacts svg {
    width: 9px;
    height: 9px;
    margin-right: 9px;
    flex: none;
    fill: var(--teal);
  }

  .back-brand {
    position: absolute;
    left: 0;
    right: 0;
    top: 160px;
    text-align: center;
  }
  .back-brand .name {
    color: var(--teal);
    font-weight: 600;
    font-size: 22px;
    line-height: 28px;
    letter-spacing: 1px;
    text-transform: uppercase;
  }
  .back-brand .underline {
    width: 276px;
    height: 1px;
    margin: 8px auto 0;
    background: var(--rule);
  }
</style>
</head>
<body>
<main class="canvas">
  <section class="card card--front">
    <div class="brand-block">Marlow Benefits Consulting</div>
    <div class="divider"></div>
    <div class="details">
      <p class="person">Gerald P Hollins <span class="role">- CEO</span></p>
      <p class="address">5172 Brackenridge Road<br>Ashford, TN 37990</p>
      <ul class="contacts">
        <li>
          <svg viewBox="0 0 10 10" aria-hidden="true"><path d="M2 0.5 L3.6 2.6 L2.8 3.6 Q4 6 6.4 7.2 L7.4 6.4 L9.5 8 L8.4 9.5 Q4.5 9.5 0.5 1.6 Z"/></svg>
          865-247-3861
        </li>
        <li>
          <svg viewBox="0 0 10 10" aria-hidden="true"><rect x="2" y="0" width="6" height="10" rx="1"/></svg>
          865-412-5593
        </li>
        <li class="email">
          <svg viewBox="0 0 10 10" aria-hidden="true"><path d="M0 2 H10 V8.5 H0 Z"/><path d="M0 2 L5 5.5 L10 2" stroke="#323335" stroke-width="1" fill="none"/></svg>
          gerald@marlowbenefits-example.com
        </li>
      </ul>
    </div>
  </section>

  <section class="card card--back">
    <div class="back-brand">
      <div class="name">Marlow Benefits Consulting</div>
      <div class="underline"></div>
    </div>
  </section>
</main>
</body>
</html>
```